VOMRA Pty Ltd Business Card

Looking for a simple yet eye-catching double-sided business card design using my company logo on one side and contact details on the other.

Target Market(s)

Government

Industry/Entity Type

Communication Systems Engineering

Contact Information for Business Card

VOMRA Pty Ltd

Requirements
Nice to have
• Would be great to have a QR code so details can be scanned into contacts

```html
<!DOCTYPE html>
<html lang="en">
<head>
<meta charset="utf-8">
<title>VOMRA Pty Ltd Business Card</title>
<link href="https://fonts.googleapis.com/css2?family=Arimo:wght@400;700&display=swap" rel="stylesheet">
<style>
  :root {
    --stage: #3b3532;
    --card-light: #f7f7f7;
    --card-dark: #2e3840;
    --ink: #2b3238;
    --ink-soft: #4a5157;
    --paper-white: #ffffff;
    --url-grey: #8a9096;
    --circuit-light-a: #e6e6e6;
    --circuit-light-b: #c9c9c9;
    --circuit-dark-a: #5b6670;
    --circuit-dark-b: #3a454e;
  }
  * { box-sizing: border-box; margin: 0; padding: 0; }
  html, body { width: 1200px; height: 716px; overflow: hidden; }
  body {
    background: var(--stage);
    font-family: "Arimo", Arial, sans-serif;
    position: relative;
  }
  .card {
    position: absolute;
    top: 208px;
    width: 520px;
    height: 300px;
    border-radius: 2px;
    box-shadow: 0 10px 24px rgba(0,0,0,0.35);
    overflow: hidden;
  }
  .card--front { left: 50px; background: var(--card-light); color: var(--ink); }
  .card--back { left: 630px; background: var(--card-dark); }

  .front__brand {
    position: absolute; left: 44px; top: 34px;
    font-size: 34px; font-weight: 700; letter-spacing: 1px; color: var(--ink);
  }
  .front__person { position: absolute; left: 44px; top: 92px; }
  .person__name { font-size: 18px; font-weight: 700; color: var(--ink-soft); }
  .person__title { font-size: 11px; color: var(--ink-soft); margin-top: 2px; }
  .front__address { position: absolute; left: 44px; top: 140px; font-size: 11px; line-height: 15px; color: var(--ink-soft); }
  .front__contacts { position: absolute; left: 44px; top: 182px; list-style: none; font-size: 11px; line-height: 16px; color: var(--ink-soft); }
  .front__contacts li { display: flex; align-items: center; gap: 6px; }
  .front__contacts svg { width: 10px; height: 10px; fill: var(--ink); }

  .front__circuit {
    position: absolute; right: 0; bottom: 0; width: 250px; height: 200px;
    background: radial-gradient(ellipse at 75% 80%, var(--circuit-light-b), var(--circuit-light-a) 60%, var(--card-light) 100%);
  }
  .back__circuit {
    position: absolute; left: 0; top: 0; width: 190px; height: 300px;
    background: radial-gradient(ellipse at 30% 45%, var(--circuit-dark-a), var(--circuit-dark-b) 65%, var(--card-dark) 100%);
  }
  .back__brand {
    position: absolute; right: 40px; bottom: 66px;
    font-size: 48px; font-weight: 700; letter-spacing: 2px; color: var(--paper-white);
  }
  .back__url {
    position: absolute; right: 40px; bottom: 44px;
    font-size: 12px; letter-spacing: 5px; color: var(--url-grey);
  }
</style>
</head>
<body>
  <section class="card card--front" aria-label="Business card front">
    <div class="front__brand">VOMRA</div>
    <div class="front__person">
      <div class="person__name">Daniel Harper</div>
      <div class="person__title">Managing Director</div>
    </div>
    <address class="front__address" style="font-style:normal">
      4120 Linden Court<br>Fairbanks, Alaska 99701
    </address>
    <ul class="front__contacts">
      <li><svg viewBox="0 0 10 10"><path d="M2 0.5l1.6 2-1 1.2a6 6 0 0 0 3.7 3.7l1.2-1 2 1.6-1 1.6C4.5 9.6 0.4 5.5 0.4 1.5z"/></svg>555-210-4837</li>
      <li><svg viewBox="0 0 10 10"><path d="M0.5 2h9v6h-9z M0.5 2l4.5 3.5L9.5 2" /></svg>info@vomrasystems.org</li>
      <li><svg viewBox="0 0 10 10"><circle cx="5" cy="5" r="4.5"/></svg>www.vomrasystems.org</li>
    </ul>
    <div class="front__circuit" role="img" aria-label="Circuit-board tree decoration with branching traces and round nodes"></div>
  </section>

  <section class="card card--back" aria-label="Business card back">
    <div class="back__circuit" role="img" aria-label="Large circuit-board tree decoration in white traces along the left edge"></div>
    <div class="back__brand">VOMRA</div>
    <div class="back__url">www.vomrasystems.org</div>
  </section>
</body>
</html>
```